Request for Business Card Design

Hi. My name is Marlene, I am looking for a new business card design for my company, Quarrow Signal Instruments, LLC. I really like the design you did for Tarsel Venture and was hoping you could do something similar using our full logo and our mark. I am also open to any raised texture design using our mark. I have attached our full logo, which would need to be somewhere on the card, as well as the mark in both outline and full form, as well as our brand colors / guide. The card does not have to be white, as long as our logo and mark appear. I actually like darker colored business cards more, but am open to all options. If you are interested in working with me, please let me know. We would also take the business card design into letterhead design if you can do that.

```html
<!DOCTYPE html>
<html lang="en">
<head>
<meta charset="utf-8">
<title>Quarrow Signal Instruments – Business Card</title>
<link href="https://fonts.googleapis.com/css2?family=Roboto:wght@400;500;700;900&display=swap" rel="stylesheet">
<style>
  :root {
    --brand-blue: #0a9ec7;
    --brand-blue-deep: #078bb0;
    --card-black: #1c1c1c;
    --stage: #2b2b2b;
    --white: #ffffff;
    --rule: #4a4a4a;
  }
  * { margin: 0; padding: 0; box-sizing: border-box; }
  html, body {
    width: 1200px; height: 689px; overflow: hidden;
    background: var(--stage);
    font-family: "Roboto", Arial, sans-serif;
  }
  .canvas { position: relative; width: 1200px; height: 689px; }
  .card {
    position: absolute; top: 190px;
    width: 540px; height: 310px;
    border-radius: 18px; overflow: hidden;
  }

  /* Front */
  .card-front { left: 40px; background: var(--brand-blue); }
  .front-brand {
    position: absolute; left: 40px; bottom: 40px; color: var(--white);
  }
  .brand-name {
    font-weight: 900; font-size: 44px; letter-spacing: 4px; line-height: 1;
  }
  .brand-sub {
    font-weight: 500; font-size: 11.5px; letter-spacing: 1.2px; margin-top: 4px;
  }

  /* Back */
  .card-back { left: 620px; background: var(--card-black); }
  .back-brand {
    position: absolute; left: 30px; top: 118px;
    display: flex; align-items: center; gap: 12px; color: var(--white);
  }
  .back-brand .brand-dot {
    width: 30px; height: 30px; border-radius: 50%; background: var(--brand-blue); flex: none;
  }
  .back-brand .brand-name { font-size: 27px; letter-spacing: 2.5px; }
  .back-brand .brand-sub { font-size: 7.4px; letter-spacing: 0.8px; margin-top: 3px; }
  .divider {
    position: absolute; left: 282px; top: 30px; width: 1px; height: 190px; background: var(--rule);
  }
  .contact { position: absolute; left: 302px; top: 34px; color: var(--white); }
  .person-name {
    color: var(--brand-blue); font-weight: 700; font-size: 21px; letter-spacing: 0.5px;
  }
  .person-role { font-size: 13px; margin-top: 2px; }
  .contact-list { list-style: none; margin-top: 16px; }
  .contact-list li {
    display: flex; align-items: center; gap: 8px; font-size: 12.5px; margin-bottom: 6px;
  }
  .contact-list svg { width: 13px; height: 13px; fill: var(--brand-blue); flex: none; }
  .address { font-size: 12.5px; line-height: 1.45; margin-top: 12px; padding-left: 21px; }
  .band-line {
    position: absolute; left: 0; right: 0; bottom: 40px; height: 4px; background: var(--brand-blue);
  }
  .band {
    position: absolute; left: 0; right: 0; bottom: 0; height: 30px; background: var(--brand-blue);
  }
</style>
</head>
<body>
<main class="canvas">
  <section class="card card-front" aria-label="Card front">
    <div class="front-brand">
      <div class="brand-name">QUARROW</div>
      <div class="brand-sub">SIGNAL INSTRUMENTS</div>
    </div>
  </section>

  <section class="card card-back" aria-label="Card back">
    <div class="back-brand">
      <span class="brand-dot"></span>
      <div>
        <div class="brand-name">QUARROW</div>
        <div class="brand-sub">SIGNAL INSTRUMENTS</div>
      </div>
    </div>
    <div class="divider"></div>
    <div class="contact">
      <div class="person-name">OWEN HARLOW</div>
      <div class="person-role">Managing Director</div>
      <ul class="contact-list">
        <li><svg viewBox="0 0 24 24" aria-hidden="true"><path d="M6.6 10.8a15 15 0 0 0 6.6 6.6l2.2-2.2a1 1 0 0 1 1-.25 11.4 11.4 0 0 0 3.6.57 1 1 0 0 1 1 1V20a1 1 0 0 1-1 1A17 17 0 0 1 3 4a1 1 0 0 1 1-1h3.5a1 1 0 0 1 1 1c0 1.25.2 2.45.57 3.57a1 1 0 0 1-.25 1z"/></svg>044-555 018 224</li>
        <li><svg viewBox="0 0 24 24" aria-hidden="true"><path d="M2 5h20v14H2z M2 5l10 8 10-8" fill="none" stroke="#0a9ec7" stroke-width="2"/></svg>info@quarrowsignal.com</li>
        <li><svg viewBox="0 0 24 24" aria-hidden="true"><circle cx="12" cy="12" r="9" fill="none" stroke="#0a9ec7" stroke-width="2"/><path d="M3 12h18M12 3c3 3 3 15 0 18M12 3c-3 3-3 15 0 18" fill="none" stroke="#0a9ec7" stroke-width="1.5"/></svg>www.quarrowsignal.com</li>
      </ul>
      <div class="address">88, Fenwick Lane<br>30917, Norland</div>
    </div>
    <div class="band-line"></div>
    <div class="band"></div>
  </section>
</main>
</body>
</html>
```